Innovative Webpage for leadership development and training company

Bright Harbor is a company supporting small organisations, in particular NGOs or projects, to increase the impact of their training and to increase the retention of talent through customized leadership development solutions. We help organisations to Guide Forward & Coach Forward
We want to have a simple but modern design webpage that stands outs from the usual consulting webpages
Here you are two possible examples of consulting firms approaching the same target audience
http://www.marlowquill.example/
http://zephvantro.example/#intro
The webpage should be designed and developed in a platform that allows full customization in the future both in terms of pages, text and images
It should allow the integration of two short videos that are currently under development
It should allow the maximum possible interoperabililty with tables and smartphones

Target Market(s)

Nonprofit, young professionals, technical assistance and capacity building projects, global SMEs, multicultural teals

Industry/Entity Type

Leadership

Number of Pages Required

5+ page

Requirements
Must have
• A dynamic/engaging/modern homepage
• A design that can be easily transferable to other pages
• A user-friendly platform that allows complete customization
• Evaluation Criteria
• 1. Overall Design/Feel of the webpage (in particular homepage). Our company looks for innovative leadership development and training. We often step out of our comfort zone in a playful positive way and that requires courage.
• 2. Flexibility to edit and/or translate homepage design to new/other pages
• 3. User-friendliness to customize, change the webpage
• 4. Completeness of coded pages (# of pages effectively developed)
Nice to have
• The maximum number of coded pages designed as per the attached file

```html
<!DOCTYPE html>
<html lang="en">
<head>
<meta charset="utf-8">
<title>Bright Harbor — Leadership Development &amp; Training</title>
<link rel="stylesheet" href="https://fonts.googleapis.com/css2?family=Raleway:wght@400;500;600;700&family=Open+Sans:ital,wght@0,400;0,600;0,700;1,400&display=swap">
<style>
:root{
  --orange:#ff6600;
  --ink:#222222;
  --text:#555555;
  --muted:#8a8a8a;
  --dark:#161616;
  --white:#ffffff;
  --line:#e4e4e4;
  --skin:#e2b896;
  --suit:#2a2f3a;
  --shirt:#a9c1dc;
  --room:#eef0f2;
  --heading:"Raleway",sans-serif;
  --body:"Open Sans",sans-serif;
}
*{box-sizing:border-box;margin:0;padding:0}
html,body{width:1200px;height:3186px;overflow:hidden;background:var(--white);font-family:var(--body);color:var(--text)}
.page{position:relative;width:1200px;height:3186px;overflow:hidden}
.abs{position:absolute}
h1,h2,h3{font-weight:400}

/* header */
.brand-box{left:164px;top:0;width:125px;height:127px;background:var(--white);box-shadow:0 2px 8px rgba(0,0,0,.18);display:flex;flex-direction:column;align-items:center;justify-content:center;gap:8px;z-index:3}
.brand-dot{width:34px;height:34px;border-radius:50%;background:var(--orange)}
.brand-name{font-family:var(--heading);font-weight:700;font-size:17px;color:var(--ink);text-align:center;line-height:1.1}
.nav{left:518px;top:76px;display:flex;font-size:11.5px;color:var(--muted)}
.nav a{color:var(--muted);text-decoration:none}
.nav a.active{color:var(--orange);font-weight:600}
.nav .sep{margin:0 22px;color:#bbb}

/* hero */
.hero-photo{left:106px;top:110px;width:988px;height:600px;
  background:
    radial-gradient(ellipse 260px 320px at 8% 30%, rgba(226,184,150,.85), transparent 70%),
    radial-gradient(ellipse 220px 200px at 40% 12%, rgba(200,210,222,.9), transparent 70%),
    radial-gradient(ellipse 260px 300px at 72% 22%, rgba(169,193,220,.95), transparent 70%),
    radial-gradient(ellipse 220px 300px at 92% 55%, rgba(240,232,226,.95), transparent 70%),
    radial-gradient(ellipse 420px 200px at 55% 92%, rgba(236,238,242,.9), transparent 70%),
    linear-gradient(120deg,#6b4a3c 0%,#3a2f32 35%,#2a2c34 60%,#4a5468 100%)}
.hero-panel{left:164px;top:289px;width:649px;height:256px;background:rgba(20,20,20,.8);padding:24px 42px}
.hero-title{font-family:var(--heading);font-weight:400;font-size:42px;color:var(--orange);line-height:1.1;white-space:nowrap}
.hero-sub{font-family:var(--heading);font-size:13px;color:#a8a8a8;margin-top:8px}
.hero-text{font-size:11px;line-height:1.6;color:#e6e6e6;margin-top:12px;width:420px}
.btn{display:inline-flex;align-items:center;justify-content:center;font-weight:600;font-size:10px;color:var(--white);background:var(--orange);text-decoration:none}
.hero-panel .btn{width:119px;height:36px;margin-top:22px}
.btn-dark{background:var(--dark)}

/* who we are */
.about-band{left:0;top:710px;width:1200px;height:375px;background:var(--orange)}
.about-photo{left:161px;top:771px;width:353px;height:270px;
  background:
    radial-gradient(ellipse 90px 130px at 50% 28%, rgba(255,255,255,.95), transparent 70%),
    radial-gradient(ellipse 120px 90px at 25% 70%, rgba(226,184,150,.8), transparent 70%),
    radial-gradient(ellipse 140px 110px at 78% 78%, rgba(42,47,58,.9), transparent 70%),
    linear-gradient(180deg,#f3f4f5 0%,#dfe2e6 55%,#6a6f78 100%)}
.about-title{left:537px;top:776px;font-family:var(--heading);font-size:30px;font-weight:400;color:var(--ink)}
.about-lead{left:537px;top:830px;width:490px;font-size:11.5px;line-height:1.55;color:var(--white)}
.about-text{left:537px;top:896px;width:490px;font-size:10px;line-height:1.55;color:#fff3ea}
.about-btn{left:537px;top:977px;width:119px;height:36px}

/* services */
.section-title{left:0;width:1200px;text-align:center;font-family:var(--heading);font-weight:400;font-size:30px;color:var(--orange)}
.section-title strong{font-weight:700}
.service{width:300px;text-align:center}
.service-photo{width:187px;height:187px;border-radius:50%;margin:0 auto}
.photo-team{background:
    radial-gradient(circle at 30% 40%, rgba(226,184,150,.9), transparent 35%),
    radial-gradient(circle at 65% 55%, rgba(42,47,58,.95), transparent 45%),
    linear-gradient(160deg,#f2f3f5 0%,#c9ced6 60%,#3e434b 100%)}
.photo-board{background:
    radial-gradient(ellipse 40px 60px at 45% 30%, rgba(255,255,255,.95), transparent 70%),
    radial-gradient(circle at 65% 45%, rgba(110,118,130,.9), transparent 35%),
    radial-gradient(circle at 30% 78%, rgba(42,47,58,.9), transparent 40%),
    linear-gradient(170deg,#eef0f2 0%,#d4d8de 55%,#5b616b 100%)}
.photo-workshop{background:
    radial-gradient(ellipse 50px 70px at 50% 25%, rgba(255,255,255,.95), transparent 70%),
    radial-gradient(circle at 55% 45%, rgba(42,47,58,.9), transparent 30%),
    radial-gradient(circle at 75% 72%, rgba(226,184,150,.8), transparent 35%),
    linear-gradient(170deg,#f3f4f5 0%,#d6dadf 55%,#4a4f58 100%)}
.service-photo.ringed{border:3px solid var(--orange)}
.service-name{font-family:var(--heading);font-size:15px;font-weight:400;color:var(--ink);margin-top:22px}
.service-name.highlight{color:var(--orange)}
.service-desc{font-size:9px;line-height:1.55;color:#555;margin:8px auto 0;width:230px}
.service .btn{width:74px;height:30px;margin-top:10px;font-size:8.5px}
.divider{left:0;top:1589px;width:1200px;height:1px;background:var(--line)}

/* video */
.video-band{left:0;top:1716px;width:1200px;height:395px;background:var(--orange)}
.video{top:1765px;height:297px}
.video-one{left:0;width:380px;background:
    radial-gradient(circle at 22% 40%, rgba(226,184,150,.9), transparent 25%),
    radial-gradient(ellipse 120px 150px at 55% 60%, rgba(30,34,42,.95), transparent 70%),
    radial-gradient(ellipse 180px 60px at 40% 92%, rgba(240,240,240,.95), transparent 70%),
    linear-gradient(160deg,#e9eaec 0%,#b7bcc3 55%,#4a4f57 100%)}
.video-two{left:382px;width:438px;background:
    radial-gradient(ellipse 60px 90px at 66% 30%, rgba(255,255,255,.95), transparent 70%),
    radial-gradient(circle at 20% 55%, rgba(226,184,150,.8), transparent 25%),
    radial-gradient(ellipse 140px 70px at 55% 88%, rgba(60,64,72,.85), transparent 70%),
    linear-gradient(160deg,#f5f5f5 0%,#d2d6db 55%,#7a8089 100%)}
.video-three{left:822px;width:378px;background:
    radial-gradient(circle at 20% 40%, rgba(226,184,150,.8), transparent 22%),
    radial-gradient(circle at 55% 35%, rgba(169,193,220,.9), transparent 25%),
    radial-gradient(ellipse 200px 70px at 50% 85%, rgba(250,250,250,.95), transparent 70%),
    linear-gradient(160deg,#f0f1f2 0%,#c8cdd3 55%,#5a5f67 100%)}
.play{position:absolute;width:60px;height:42px;border-radius:8px}
.play-orange{background:var(--orange)}
.play-dark{background:#111}
.play::after{content:"";position:absolute;left:24px;top:12px;border-left:16px solid var(--white);border-top:9px solid transparent;border-bottom:9px solid transparent}
.play-caption{position:absolute;width:100%;text-align:center;font-size:12px;color:var(--ink)}

/* clients */
.clients-intro{left:0;top:2214px;width:1200px;text-align:center;font-size:10.5px;line-height:1.6;color:#666}
.carousel-arrows{left:1020px;top:2272px}
.clients-box{left:161px;top:2296px;width:878px;height:149px;border:1px solid #dcdcdc;background:var(--white);display:flex;align-items:center;justify-content:space-around;padding:0 20px}
.client{display:flex;align-items:center;gap:10px;font-family:var(--heading);font-weight:600;font-size:20px;color:#2a4a8a}
.client-mark{width:22px;height:22px;border-radius:50%;background:#2a4a8a}

/* testimonials */
.testimonials{left:0;top:2506px;width:1200px;height:464px;background:var(--dark)}
.testimonials .section-title{top:38px}
.quote-icon{left:578px;top:116px}
.quote-text{left:250px;top:180px;width:700px;text-align:center;font-style:italic;font-size:12px;line-height:1.7;color:#d6d6d6}
.avatar{left:562px;top:251px;width:76px;height:76px;border-radius:50%;border:3px solid var(--orange);background:radial-gradient(circle at 50% 40%,#e2b896 0%,#b98d6e 45%,#f2f2f2 75%)}
.quote-name{left:0;top:352px;width:1200px;text-align:center;font-size:12px;font-weight:700;color:var(--orange)}
.quote-role{left:0;top:378px;width:1200px;text-align:center;font-size:9.5px;color:#bdbdbd}
.dots{left:570px;top:428px;display:flex;gap:8px}
.dots span{width:14px;height:14px;border-radius:50%;background:#d9d9d9}
.dots span.on{background:var(--orange)}

/* footer */
.footer-brand{left:0;top:3010px;width:1200px;display:flex;flex-direction:column;align-items:center;gap:6px}
.footer-brand .brand-dot{width:26px;height:26px}
.social{left:558px;top:3094px;display:flex;gap:8px}
.social span{width:22px;height:22px;border-radius:50%;background:#cfcfcf}
.social span.primary{background:#2b5aa8}
.footer-mail{left:0;top:3126px;width:1200px;text-align:center;font-size:10px;color:#555}
.footer-line{left:0;top:3154px;width:1200px;height:1px;background:var(--line)}
.copyright{left:0;top:3163px;width:1200px;text-align:center;font-size:9px;color:#777}
</style>
</head>
<body>
<div class="page">

  <header>
    <div class="abs brand-box">
      <span class="brand-dot"></span>
      <span class="brand-name">Bright Harbor</span>
    </div>
    <nav class="abs nav">
      <a class="active" href="#">Home</a><span class="sep">/</span>
      <a href="#">About Us</a><span class="sep">/</span>
      <a href="#">Services</a><span class="sep">/</span>
      <a href="#">Testimonials</a><span class="sep">/</span>
      <a href="#">Blog</a><span class="sep">/</span>
      <a href="#">Contact Us</a>
    </nav>
  </header>

  <section>
    <div class="abs hero-photo" role="img" aria-label="Team of business people working together at a meeting table with a laptop and charts"></div>
    <div class="abs hero-panel">
      <h1 class="hero-title">Welcome To Our Company</h1>
      <p class="hero-sub">Consulting - Training - Coaching</p>
      <p class="hero-text">Bright Harbor Sprl. offers tailor made innovative solutions for organisational and individual excellence. We strive to transform the capacity and impact of non-profit organizations</p>
      <a class="btn" href="#">Read More</a>
    </div>
  </section>

  <section>
    <div class="abs about-band"></div>
    <div class="abs about-photo" role="img" aria-label="Trainer presenting at a flipchart to a seated group in a bright meeting room"></div>
    <h2 class="abs about-title">Who We Are ?</h2>
    <p class="abs about-lead">Bright Harbor Sprl. offers tailor made innovative solutions for organisational and individual excellence. We strive to transform the capacity and impact of non-profit organizations</p>
    <p class="abs about-text">Bright Harbor Sprl. offers tailor made innovative solutions for organisational and individual excellence. We strive to transform the capacity and impact of non-profit organizations, international development and public-private projects and SMEs through customised services in leadership development, executive coaching and training.</p>
    <a class="abs btn btn-dark about-btn" href="#">Read More</a>
  </section>

  <section>
    <h2 class="abs section-title" style="top:1138px">Our Services</h2>
    <div class="abs service" style="left:150px;top:1206px">
      <div class="service-photo photo-team ringed" role="img" aria-label="Business team in discussion around a table"></div>
      <h3 class="service-name highlight">Organisational Development</h3>
      <p class="service-desc">Bright Harbor's leadership and management development programs help managers develop themselves...</p>
      <a class="btn btn-dark" href="#">Read More</a>
    </div>
    <div class="abs service" style="left:451px;top:1206px">
      <div class="service-photo photo-board" role="img" aria-label="Coach presenting at a whiteboard to a small audience"></div>
      <h3 class="service-name">Executive Coaching</h3>
      <p class="service-desc">Bright Harbor's coaching programs, which are either face-to-face or by video call, help middle managers and senior leaders...</p>
      <a class="btn" href="#">Read More</a>
    </div>
    <div class="abs service" style="left:751px;top:1206px">
      <div class="service-photo photo-workshop" role="img" aria-label="Trainer leading a workshop with seated participants"></div>
      <h3 class="service-name">Training</h3>
      <p class="service-desc">His experience includes coaching senior leaders working in multicultural teams in banking, insurance, international trade...</p>
      <a class="btn" href="#">Read More</a>
    </div>
    <div class="abs divider"></div>
  </section>

  <section>
    <h2 class="abs section-title" style="top:1639px">View Our <strong>Training Video</strong></h2>
    <div class="abs video-band"></div>
    <div class="abs video video-one" role="img" aria-label="Video still: colleagues talking at a conference table">
      <span class="play play-orange" style="left:130px;top:128px"></span>
    </div>
    <div class="abs video video-two" role="img" aria-label="Video still: workshop group listening to a presenter">
      <span class="play play-dark" style="left:189px;top:108px"></span>
      <span class="play-caption" style="top:172px">Click here To Play</span>
    </div>
    <div class="abs video video-three" role="img" aria-label="Video still: multicultural team meeting around a table">
      <span class="play play-orange" style="left:190px;top:128px"></span>
    </div>
  </section>

  <section>
    <h2 class="abs section-title" style="top:2163px">Our Clients</h2>
    <p class="abs clients-intro">Non-profit organisations: Many NGOs have an international or global mandate supported by a slim<br>organizational structure.</p>
    <svg class="abs carousel-arrows" width="20" height="14" viewBox="0 0 20 14" aria-hidden="true">
      <path d="M7 2 L2 7 L7 12" fill="none" stroke="#ff6600" stroke-width="2"/>
      <path d="M13 2 L18 7 L13 12" fill="none" stroke="#ff6600" stroke-width="2"/>
    </svg>
    <div class="abs clients-box">
      <span class="client"><span class="client-mark"></span>Ridgeline Civic Alliance</span>
      <span class="client">Lumora for Causes</span>
      <span class="client">Kessel Hokuto</span>
      <span class="client">Clearpath Care</span>
    </div>
  </section>

  <section class="abs testimonials">
    <h2 class="abs section-title">Testimonials</h2>
    <svg class="abs quote-icon" width="44" height="34" viewBox="0 0 44 34" aria-hidden="true">
      <path d="M2 34V18C2 8 8 2 18 0v7c-5 2-7 5-7 10h7v17zM26 34V18C26 8 32 2 42 0v7c-5 2-7 5-7 10h7v17z" fill="#ff6600"/>
    </svg>
    <p class="abs quote-text">Tomas's professionalism and dedication to his field is remarkable as is his strength and confidence as a coach. A careful listener, Mr. Valdren helped each of the training participants individually and uniquely, focused on developing confident skilled coaches...</p>
    <div class="abs avatar" role="img" aria-label="Portrait of the client giving the testimonial"></div>
    <p class="abs quote-name">Mr. TV.</p>
    <p class="abs quote-role">Training Director, Executive Search and HR Consulting, China</p>
    <div class="abs dots"><span></span><span class="on"></span><span></span></div>
  </section>

  <footer>
    <div class="abs footer-brand">
      <span class="brand-dot"></span>
      <span class="brand-name">Bright Harbor</span>
    </div>
    <div class="abs social" aria-label="Social links">
      <span class="primary"></span><span></span><span></span>
    </div>
    <p class="abs footer-mail">&#9993; info@brightharbor.example</p>
    <div class="abs footer-line"></div>
    <p class="abs copyright">© All Copyrights Reserved 2015</p>
  </footer>

</div>
</body>
</html>
```